New Innovative Counselling and psychotherapy Service needs Business Card design

Keep it simple and professional. On one side, just company name and logo (perhaps in all blue) and maybe a tag line.

On other side (all white) my name and Qualifications in centre

Industry/Entity Type

Health And Wellness

Contact Information for Business Card

Dara Whelby
Counsellor & Psychotherapist
BSc (Psychol.), BA, Dip. (Couns. & Psych.), PG.Cert (CBT), FGTrK, ONRE

I will also require Mobile no, Email and web site address of which I'll pass on to final designer.

Font styles to use
Sans Serif

Requirements
Must have
• My Logo Only and please use the colours in logo that is in it.
Should not have
• Any other images

```html
<!DOCTYPE html>
<html lang="en">
<head>
<meta charset="utf-8">
<title>Stillwater Lane – Business Card</title>
<link href="https://fonts.googleapis.com/css2?family=Open+Sans:wght@300;400;600;700&display=swap" rel="stylesheet">
<style>
  :root {
    --backdrop: #2b2d30;
    --sky-light: #74dcf8;
    --sky: #3fb0ec;
    --sky-deep: #2f9fe0;
    --leaf: #8dcf4f;
    --paper: #f4f5f6;
    --ink-grey: #4a4f55;
    --tagline: #3e6c8c;
    --white: #ffffff;
  }
  * { margin: 0; padding: 0; box-sizing: border-box; }
  html, body { width: 1200px; height: 900px; overflow: hidden; }
  body {
    background: var(--backdrop);
    font-family: "Open Sans", Arial, sans-serif;
    display: flex; flex-direction: column; align-items: center; justify-content: center; gap: 40px;
  }
  .card { width: 700px; height: 400px; position: relative; overflow: hidden; box-shadow: 0 12px 30px rgba(0,0,0,.45); }

  /* Front */
  .card-front {
    background: linear-gradient(120deg, var(--sky-light) 0%, var(--sky) 45%, var(--sky-deep) 100%);
    display: flex; flex-direction: column; align-items: center;
  }
  .front-brand { margin-top: 120px; display: flex; align-items: center; gap: 22px; }
  .brand-dot { width: 90px; height: 90px; border-radius: 50%; background: var(--white); }
  .front-brand .brand-name { color: var(--white); font-size: 40px; font-weight: 400; }
  .tagline { position: absolute; bottom: 58px; width: 100%; text-align: center; color: var(--tagline); font-size: 17px; font-weight: 400; }

  /* Back */
  .card-back { background: var(--paper); }
  .back-band { position: absolute; inset: 0; }
  .back-brand { position: absolute; left: 175px; top: 118px; display: flex; align-items: center; gap: 16px; }
  .back-brand .brand-dot { width: 52px; height: 52px; background: var(--sky); }
  .back-brand .brand-name { color: var(--ink-grey); font-size: 34px; font-weight: 400; }
  .corner-dot { position: absolute; right: 40px; top: 42px; width: 110px; height: 110px; border-radius: 50%; background: var(--white); }

  .person { position: absolute; right: 378px; top: 262px; text-align: right; color: var(--white); }
  .person-name { font-size: 22px; font-weight: 700; text-transform: uppercase; letter-spacing: .5px; }
  .person-role { font-size: 17px; font-weight: 400; text-transform: uppercase; }
  .person-quals { font-size: 12px; font-weight: 400; line-height: 1.35; margin-top: 2px; }
  .divider { position: absolute; left: 345px; top: 232px; width: 1px; height: 120px; background: rgba(255,255,255,.7); }
  .contact { position: absolute; left: 365px; top: 228px; list-style: none; color: var(--white); font-size: 15px; }
  .contact li { display: flex; align-items: center; gap: 10px; height: 24px; }
  .contact svg { width: 14px; height: 14px; flex: none; }
</style>
</head>
<body>

<section class="card card-front">
  <div class="front-brand">
    <span class="brand-dot"></span>
    <span class="brand-name">Stillwater Lane</span>
  </div>
  <p class="tagline">Caring For Your Psychological Well-Being Is Our Top Priority</p>
</section>

<section class="card card-back">
  <svg class="back-band" viewBox="0 0 700 400" preserveAspectRatio="none" aria-hidden="true">
    <defs>
      <linearGradient id="bandFill" x1="0" y1="0" x2="1" y2="1">
        <stop offset="0" stop-color="#45b6ee"/>
        <stop offset="1" stop-color="#2f9fe0"/>
      </linearGradient>
    </defs>
    <polygon points="0,232 520,232 600,100 700,100 700,400 0,400" fill="url(#bandFill)"/>
  </svg>

  <div class="back-brand">
    <span class="brand-dot"></span>
    <span class="brand-name">Stillwater Lane</span>
  </div>
  <span class="corner-dot"></span>

  <div class="person">
    <p class="person-name">Dara Whelby</p>
    <p class="person-role">Counsellor &amp; Psychotherapist</p>
    <p class="person-quals">BSc (Psychol.), BA, Dip. (Couns. &amp; Psych.)<br>PG.Cert (CBT), FGTrK, ONRE</p>
  </div>

  <span class="divider"></span>

  <ul class="contact">
    <li>
      <svg viewBox="0 0 14 14"><rect x="3" y="0.8" width="8" height="12.4" rx="1.5" fill="none" stroke="#fff" stroke-width="1.4"/><circle cx="7" cy="10.8" r=".9" fill="#fff"/></svg>
      555 210 4478
    </li>
    <li>
      <svg viewBox="0 0 14 14"><rect x="0.8" y="2.5" width="12.4" height="9" fill="none" stroke="#fff" stroke-width="1.4"/><polyline points="1,3 7,8 13,3" fill="none" stroke="#fff" stroke-width="1.4"/></svg>
      dara@stillwaterlane.com
    </li>
    <li>
      <svg viewBox="0 0 14 14"><circle cx="7" cy="7" r="6" fill="none" stroke="#fff" stroke-width="1.4"/><ellipse cx="7" cy="7" rx="2.6" ry="6" fill="none" stroke="#fff" stroke-width="1.1"/><line x1="1" y1="7" x2="13" y2="7" stroke="#fff" stroke-width="1.1"/></svg>
      www.stillwaterlane.com
    </li>
  </ul>
</section>

</body>
</html>
```